Vegetable Grower Expo Backdrop

I need an 8x8 backdrop for an expo booth. We are a vegetable grower and have very limited graphics to work with. I have uploaded our logo which may not be the correct format and need to be updated for quality to print at that size. Need something quick and simple. Expo is August 18th

Target Market(s)

Retail and Wholesale buyers

Industry/Entity Type

Produce

Colors

Designer to choose colors to be used in the design.

Requirements
Must have
• Logo
Nice to have
• I am open to ideas!
Should not have
• Keep it simple and bottom 1/4 will be covered with samples so focus on top 3/4 of banner

```html
<!DOCTYPE html>
<html lang="en">
<head>
<meta charset="utf-8">
<title>Ridgeline Growers – Expo Backdrop</title>
<link rel="stylesheet" href="https://fonts.googleapis.com/css2?family=Roboto+Condensed:wght@300;400;700&display=swap">
<style>
  :root {
    --page: #e9e9e9;
    --paper: #f4f4f4;
    --ink: #141414;
    --grey-text: #5a5a5a;
    --title-green: #16902c;
    --field-green: #44a12e;
    --field-green-deep: #3a9226;
    --accent-yellow: #f1e600;
    --tag-border: #6e6e6e;
  }
  * { box-sizing: border-box; margin: 0; padding: 0; }
  html, body {
    width: 1129px; height: 1200px; overflow: hidden;
    background: var(--page);
    font-family: "Roboto Condensed", "Arial Narrow", sans-serif;
  }
  .backdrop {
    position: absolute; left: 40px; top: 76px;
    width: 1049px; height: 1049px;
    background: var(--paper);
    overflow: hidden;
  }
  .field {
    position: absolute; left: 0; top: 0; width: 1049px; height: 1049px;
  }
  .brand {
    position: absolute; left: 54px; top: 52px;
    display: flex; align-items: center; gap: 12px;
    color: var(--ink); font-weight: 700; font-size: 34px;
    line-height: 1; letter-spacing: 1px; text-transform: uppercase;
  }
  .brand-dot {
    width: 26px; height: 26px; border-radius: 50%; background: var(--field-green);
  }
  .brand-name { display: flex; flex-direction: column; }
  .tags {
    position: absolute; left: 765px; top: 36px;
    display: flex; flex-direction: column; gap: 6px;
  }
  .tag {
    width: 234px; height: 37px;
    border: 1.5px solid var(--tag-border); border-radius: 5px;
    background: #fff;
    display: flex; align-items: center; gap: 8px; padding-left: 10px;
    font-size: 25px; font-weight: 300; color: var(--grey-text);
  }
  .tag::before {
    content: ""; border-left: 7px solid var(--grey-text);
    border-top: 5px solid transparent; border-bottom: 5px solid transparent;
  }
  .tag b { font-weight: 300; color: var(--title-green); }
  .headline {
    position: absolute; left: 0; width: 100%; text-align: center; top: 160px;
    line-height: 1;
  }
  .headline-top {
    display: block; font-size: 80px; font-weight: 400; color: var(--ink);
  }
  .headline-main {
    display: block; margin-top: 0; font-size: 128px; font-weight: 400;
    color: var(--title-green); letter-spacing: -1px;
  }
  .produce-basket {
    position: absolute; left: 256px; top: 354px; width: 528px; height: 453px;
    border-radius: 48% 48% 42% 42% / 38% 38% 60% 60%;
    background:
      radial-gradient(ellipse at 50% 32%, #d8402a 0%, #c95a2a 22%, transparent 48%),
      radial-gradient(ellipse at 22% 38%, #5e9a34 0%, transparent 40%),
      radial-gradient(ellipse at 50% 75%, #b8803f 0%, #9c6428 55%, #7f4f1f 100%);
  }
  .contact {
    position: absolute; display: flex; align-items: center; gap: 10px; color: #fff;
  }
  .contact-phone { left: 66px; top: 704px; }
  .contact-web { left: 758px; top: 724px; }
  .contact-lines { display: flex; flex-direction: column; line-height: 1.05; }
  .contact-label { font-size: 13px; font-weight: 300; }
  .contact-value { font-size: 30px; font-weight: 300; }
  .contact-web .contact-value { font-size: 24px; }
</style>
</head>
<body>
  <main class="backdrop">
    <svg class="field" viewBox="0 0 1049 1049" aria-hidden="true">
      <path fill="var(--field-green)" d="M0 560 L18 548 L30 562 L52 552 L60 568 L82 566 L98 584 L120 580 L138 596 L170 598 L196 614 L230 616 L262 628 L300 626 L330 620 L380 618 L440 616 L520 612 L640 606 L720 590 L760 584 L790 570 L820 572 L850 550 L872 556 L896 534 L918 540 L936 518 L958 520 L972 500 L990 504 L1004 482 L1020 488 L1032 468 L1049 460 L1049 1049 L0 1049 Z"/>
      <path fill="var(--field-green)" d="M960 500 L985 470 L1000 478 L1030 452 L1049 448 L1049 470 L1020 478 L998 494 Z"/>
      <path fill="var(--field-green)" d="M22 540 L40 526 L48 536 L34 552 Z"/>
    </svg>

    <div class="brand">
      <span class="brand-dot"></span>
      <span class="brand-name"><span>Ridgeline</span><span>Growers</span></span>
    </div>

    <div class="tags">
      <div class="tag">Produce <b>Everyday</b></div>
      <div class="tag">Quality <b>Guaranteed</b></div>
    </div>

    <h1 class="headline">
      <span class="headline-top">FARM FRESH</span>
      <span class="headline-main">VEGETABLES</span>
    </h1>

    <div class="produce-basket" role="img" aria-label="Photograph of a wicker basket filled with fresh vegetables: lettuce, peppers, tomatoes, potatoes, zucchini and eggplant"></div>

    <div class="contact contact-phone">
      <svg width="46" height="46" viewBox="0 0 46 46" aria-hidden="true">
        <circle cx="23" cy="23" r="23" fill="var(--accent-yellow)"/>
        <path fill="var(--field-green-deep)" d="M15 11c1.5-1 3-.6 3.8.8l2.4 4.4c.6 1.1.3 2.4-.7 3.1l-1.6 1.1c1 2.6 3 4.8 5.6 6l1.2-1.5c.8-1 2.1-1.2 3.2-.6l4.3 2.5c1.3.8 1.6 2.4.7 3.7-1.6 2.4-3.8 3.6-6.6 2.8-7-2-12.6-7.8-14.4-14.8-.6-2.6.6-5.1 2.1-6.5z"/>
      </svg>
      <div class="contact-lines">
        <span class="contact-label">Call to Find Out More</span>
        <span class="contact-value">+012 555 018</span>
      </div>
    </div>

    <div class="contact contact-web">
      <svg width="24" height="24" viewBox="0 0 24 24" aria-hidden="true">
        <circle cx="12" cy="12" r="12" fill="var(--accent-yellow)"/>
        <path fill="var(--field-green-deep)" d="M8 6 L17 13 L13 13.5 L15 18 L13 19 L11 14.5 L8 17 Z"/>
      </svg>
      <span class="contact-value">www.ridgelinegrowers.com</span>
    </div>
  </main>
</body>
</html>
```